Corporate Business Card

Very professional, Modern, Not to busy, include phone address email, website
(253) 617-4930, 18761 52nd Avenue S, Kent, WA 98047, martin@plumlinegroup.com, varkoworks.com

Target Market(s)

Manufacturing

Industry/Entity Type

Aero, machining, manufacturing, Off road racing

Contact Information for Business Card

Phone, address email, website

```html
<!DOCTYPE html>
<html lang="en">
<head>
<meta charset="UTF-8">
<title>Varko Works – Business Card</title>
<link href="https://fonts.googleapis.com/css2?family=Open+Sans:wght@400;600;700;800&display=swap" rel="stylesheet">
<style>
  :root {
    --backdrop: #8a8a88;
    --navy: #1b3a70;
    --navy-deep: #22366b;
    --red: #d0232a;
    --white: #ffffff;
    --ink-light: #e8ecf5;
  }
  * { margin: 0; padding: 0; box-sizing: border-box; }
  html, body {
    width: 1200px; height: 801px; overflow: hidden;
    background: var(--backdrop);
    font-family: "Open Sans", Arial, sans-serif;
  }
  .stage { position: relative; width: 1200px; height: 801px; }
  .card {
    position: absolute; top: 257px;
    width: 500px; height: 286px;
    border-radius: 18px; overflow: hidden;
    border: 1px solid var(--red);
  }
  .card--front { left: 70px; background: var(--navy); }
  .card--back { left: 630px; background: var(--navy-deep); }
  .card__shape { position: absolute; inset: 0; }

  .brand { position: absolute; font-weight: 800; line-height: 1; }
  .brand__main { display: block; font-size: 50px; letter-spacing: 1px; }
  .brand__sub { display: block; font-size: 17px; letter-spacing: 6px; margin-top: 4px; padding-left: 120px; }
  .card--front .brand { left: 42px; top: 52px; color: var(--navy); }
  .card--back .brand { left: 100px; top: 96px; color: var(--white); }
  .brand__rule { position: absolute; height: 2px; }
  .card--front .brand__rule { left: 42px; top: 140px; width: 150px; background: var(--navy); }
  .card--back .brand__rule { left: 78px; top: 182px; width: 170px; background: var(--white); }

  .contact-address {
    position: absolute; right: 245px; top: 222px;
    text-align: right; color: var(--ink-light);
    font-size: 12.5px; line-height: 17px;
  }
  .contact-address__name { color: var(--red); font-weight: 600; }
  .contact-divider {
    position: absolute; left: 266px; top: 205px;
    width: 1.5px; height: 66px; background: var(--red);
  }
  .contact-lines {
    position: absolute; left: 282px; top: 176px;
    list-style: none; color: var(--ink-light);
    font-size: 12.5px; line-height: 19px;
  }
  .contact-lines li { display: flex; align-items: center; gap: 7px; }
  .contact-lines svg { width: 11px; height: 11px; flex: none; }
</style>
</head>
<body>
<main class="stage">

  <section class="card card--front" aria-label="Business card front">
    <svg class="card__shape" viewBox="0 0 500 286" aria-hidden="true">
      <path d="M0,0 H340 C312,96 200,186 0,214 Z" fill="var(--white)"/>
      <path d="M351,0 C323,102 208,194 0,222" fill="none" stroke="var(--red)" stroke-width="2.5"/>
    </svg>
    <div class="brand">
      <span class="brand__main">VARKO</span>
      <span class="brand__sub">WORKS</span>
    </div>
    <div class="brand__rule"></div>

    <div class="contact-address">
      <div class="contact-address__name">Varko Works</div>
      <div>18761 52nd Avenue S</div>
      <div>Kent, WA 98047</div>
    </div>
    <div class="contact-divider"></div>
    <ul class="contact-lines">
      <li>
        <svg viewBox="0 0 12 12" aria-hidden="true"><path d="M2.5 1h2l1 3-1.4 1a6.5 6.5 0 0 0 3 3l1-1.4 3 1v2a1 1 0 0 1-1 1A10 10 0 0 1 1.5 2a1 1 0 0 1 1-1z" fill="var(--red)"/></svg>
        (253) 617-4930
      </li>
      <li>
        <svg viewBox="0 0 12 12" aria-hidden="true"><rect x="0.5" y="2" width="11" height="8" rx="1" fill="var(--red)"/><path d="M1 3l5 3.5L11 3" fill="none" stroke="var(--navy)" stroke-width="1"/></svg>
        martin@plumlinegroup.com
      </li>
      <li>
        <svg viewBox="0 0 12 12" aria-hidden="true"><circle cx="6" cy="6" r="5.5" fill="var(--red)"/><path d="M0.5 6h11M6 0.5c-2.5 3-2.5 8 0 11M6 0.5c2.5 3 2.5 8 0 11" fill="none" stroke="var(--navy)" stroke-width="0.9"/></svg>
        varkoworks.com
      </li>
    </ul>
  </section>

  <section class="card card--back" aria-label="Business card back">
    <div class="brand">
      <span class="brand__main">VARKO</span>
      <span class="brand__sub">WORKS</span>
    </div>
    <div class="brand__rule"></div>
  </section>

</main>
</body>
</html>
```